Corporate Travel Technology Company needs new Business Card design

We need a new business card design to reflect our re-branded company. Our company is called Tolven (pronounced tolvenn) and we provide Business Intelligence and mobile travel management solutions for the corporate travel industry. Our multinational customers use our solutions to manage large travel budgets and frequent travellers, as well as to save money and reduce risk. We'd like to see designs that use the blue and green palette as well as our corporate logo (attached below). The design should communicate innovation, insight, forward thinking, contemporary, trusted.

Target Market(s)

Large multinational corporates and Travel Agencies.

Industry/Entity Type

Business

Contact Information for Business Card

Rosalind Mercer
Chief Executive
Tolven
Phone number - +61 (0)2 8134 2907
Email address - rosalind.mercer@tolven-example.com
Mobile number - +61 (0)438 516 702
www.tolven-example.com

Font styles to use
Other font styles liked:
• Please use font as close to corporate logo as possible

Colors
0255a3
0393ce
00a990
33b8a4
33a6d7
3176b5

Requirements
Must have
• Please include the words;
• Mobile Travel Management
• Accelerating Travel Business Insights
• Use corporate logo - although icon can be stylised if needed

```html
<!DOCTYPE html>
<html lang="en">
<head>
<meta charset="utf-8">
<title>Tolven — Business Card</title>
<link rel="stylesheet" href="https://fonts.googleapis.com/css2?family=Arimo:wght@400;700&display=swap">
<style>
  :root {
    --page-bg: #e9eaea;
    --card-slate: #5c6868;
    --card-white: #ffffff;
    --brand-blue: #1db0e8;
    --ink-grey: #4f5a5a;
    --text-light: #ffffff;
    --shadow: rgba(0, 0, 0, 0.18);
  }
  * { box-sizing: border-box; margin: 0; padding: 0; }
  html, body {
    width: 1200px;
    height: 950px;
    overflow: hidden;
    background: var(--page-bg);
    font-family: "Arimo", Arial, sans-serif;
  }
  .canvas {
    position: relative;
    width: 1200px;
    height: 950px;
  }
  .card {
    position: absolute;
    left: 250px;
    width: 700px;
    height: 400px;
    overflow: hidden;
    box-shadow: 0 6px 18px var(--shadow);
  }

  /* Back of card */
  .card-back {
    top: 45px;
    background: var(--card-slate);
  }
  .back-mark {
    position: absolute;
    top: 118px;
    left: 0;
    width: 100%;
    display: flex;
    justify-content: center;
    align-items: center;
    gap: 14px;
  }
  .back-mark .mark-dot {
    width: 20px;
    height: 20px;
    border-radius: 50%;
    background: var(--brand-blue);
  }
  .back-mark .wordmark {
    font-size: 56px;
    font-weight: 400;
    color: var(--text-light);
    letter-spacing: 1px;
  }
  .back-tagline {
    position: absolute;
    top: 222px;
    left: 0;
    width: 100%;
    text-align: center;
    font-size: 15px;
    color: var(--text-light);
    letter-spacing: 0.3px;
  }
  .back-tagline .sep { color: var(--brand-blue); padding: 0 4px; }

  /* Front of card */
  .card-front {
    top: 505px;
    background: var(--card-white);
  }
  .front-shape {
    position: absolute;
    inset: 0;
  }
  .front-logo {
    position: absolute;
    top: 112px;
    left: 52px;
    display: flex;
    align-items: center;
    gap: 12px;
  }
  .front-logo .mark-dot {
    width: 18px;
    height: 18px;
    border-radius: 50%;
    background: var(--brand-blue);
  }
  .front-logo .wordmark {
    font-size: 58px;
    font-weight: 400;
    color: var(--ink-grey);
    letter-spacing: 1px;
  }
  .person {
    position: absolute;
    left: 40px;
    top: 318px;
    color: var(--text-light);
  }
  .person .name {
    font-size: 22px;
    font-weight: 700;
  }
  .person .role {
    margin-top: 5px;
    font-size: 16px;
  }
  .contacts {
    position: absolute;
    right: 26px;
    top: 186px;
    list-style: none;
    color: var(--text-light);
    font-size: 15px;
    text-align: right;
  }
  .contacts li {
    display: flex;
    justify-content: flex-end;
    align-items: center;
    gap: 8px;
    height: 22px;
  }
  .contacts svg {
    width: 14px;
    height: 14px;
    flex: none;
  }
</style>
</head>
<body>
<main class="canvas">

  <section class="card card-back" aria-label="Card back">
    <div class="back-mark">
      <span class="mark-dot"></span>
      <span class="wordmark">Tolven</span>
    </div>
    <p class="back-tagline">Mobile Travel Management<span class="sep">»</span>Accelerating Travel Business Insights</p>
  </section>

  <section class="card card-front" aria-label="Card front">
    <svg class="front-shape" width="700" height="400" viewBox="0 0 700 400" aria-hidden="true">
      <path d="M0,274 H322 C358,274 352,150 392,150 H420 C430,150 432,166 440,166 V400 H0 Z" fill="#4f5a5a"/>
      <path d="M0,290 H330 C366,290 360,166 400,166 H700 V400 H0 Z" fill="#1db0e8"/>
    </svg>

    <div class="front-logo">
      <span class="mark-dot"></span>
      <span class="wordmark">Tolven</span>
    </div>

    <ul class="contacts">
      <li>+61 (0)2 8134 2907
        <svg viewBox="0 0 16 16"><path d="M3 2h3l1 3-2 1.5a8 8 0 0 0 4.5 4.5L11 9l3 1v3a1 1 0 0 1-1 1A12 12 0 0 1 2 3a1 1 0 0 1 1-1z" fill="#fff"/></svg>
      </li>
      <li>+61 (0)438 516 702
        <svg viewBox="0 0 16 16"><rect x="4" y="1" width="8" height="14" rx="1.5" fill="none" stroke="#fff" stroke-width="1.6"/><circle cx="8" cy="12.5" r="0.9" fill="#fff"/></svg>
      </li>
      <li>rosalind.mercer@tolven-example.com
        <svg viewBox="0 0 16 16"><rect x="1" y="3" width="14" height="10" rx="1" fill="#fff"/><path d="M1.5 3.8 8 9l6.5-5.2" fill="none" stroke="#1db0e8" stroke-width="1.3"/></svg>
      </li>
      <li>www.tolven-example.com
        <svg viewBox="0 0 16 16"><circle cx="8" cy="8" r="6.5" fill="none" stroke="#fff" stroke-width="1.5"/><ellipse cx="8" cy="8" rx="2.8" ry="6.5" fill="none" stroke="#fff" stroke-width="1.2"/><path d="M1.5 8h13" stroke="#fff" stroke-width="1.2"/></svg>
      </li>
    </ul>

    <div class="person">
      <p class="name">Rosalind Mercer</p>
      <p class="role">Chief Executive</p>
    </div>
  </section>

</main>
</body>
</html>
```